Compnay PowerPoint Tempalte Design

I am needing a good base design and slide designs for interior and exterior company presentations. The template will need to be on the company brand with proper coloring and fonts. Able to be creative with layout options with a good example attached.
website for reference: www.crewvlt.com/

Target Market(s)

Professionals

Font styles to use
Other font styles liked:
• Helvetica

Requirements
Must have
• On Brand Colors, Clean, simple design

```html
<!DOCTYPE html>
<html lang="en">
<head>
<meta charset="utf-8">
<title>VLT Presentation Template</title>
<link rel="stylesheet" href="https://fonts.googleapis.com/css2?family=Arimo:wght@400;700&display=swap">
<style>
  :root {
    --page: #3b3b3b;
    --teal: #2b8f8a;
    --teal-band: #3a8a7c;
    --blue: #14628f;
    --blue-deep: #0f5585;
    --green: #6cbf1f;
    --cyan: #1fb3c8;
    --royal: #1f6fd0;
    --ink: #1c1c1c;
    --text: #333;
    --white: #fff;
    --star: #f5a623;
  }
  html, body { margin: 0; padding: 0; overflow: hidden; }
  body { width: 1200px; height: 3839px; background: var(--page); font-family: "Arimo", Helvetica, Arial, sans-serif; }
  .canvas { position: relative; width: 1200px; height: 3839px; overflow: hidden; background: var(--page); }
  .slide { position: absolute; left: 80px; width: 1040px; height: 584px; overflow: hidden; }
  .abs { position: absolute; margin: 0; }
  .photo-teal { background: linear-gradient(120deg, #2f9890 0%, #23808d 45%, #1b6c94 100%); }
  .brand-mark { position: absolute; font-weight: 700; letter-spacing: 1px; }

  /* slide 1 */
  .welcome { top: 46px; }
  .welcome h1 { left: 55px; top: 160px; font-size: 62px; color: var(--white); font-weight: 700; }
  .welcome .lead { left: 55px; top: 268px; width: 520px; font-size: 13px; line-height: 35px; color: var(--white); }
  .social { left: 55px; top: 345px; display: flex; gap: 6px; }
  .social span { width: 27px; height: 27px; border: 1.5px solid var(--white); border-radius: 50%; box-sizing: border-box; }
  .welcome .big-name { left: 650px; top: 380px; font-size: 150px; color: var(--ink); line-height: 1; }

  /* slide 2 */
  .about { top: 671px; background: var(--white); }
  .about h2 { left: 640px; top: 92px; font-size: 56px; color: var(--blue); font-weight: 700; }
  .about .body { left: 640px; top: 164px; width: 370px; font-size: 12.5px; line-height: 34.5px; color: var(--text); }
  .about .brand-mark { right: 20px; bottom: 14px; font-size: 28px; color: var(--ink); }

  /* slide 3 */
  .testimonials { top: 1297px; }
  .testimonials h2 { left: 0; width: 1262px; text-align: center; top: 90px; font-size: 56px; color: var(--blue-deep); font-weight: 700; }
  .quote-mark { font-size: 28px; color: var(--teal-band); font-weight: 700; width: 1060px; text-align: center; left: 0; }
  .testimonials .body { left: 320px; width: 420px; top: 193px; text-align: center; font-size: 12.5px; line-height: 34.5px; color: var(--text); }
  .testimonials .tag { left: 300px; width: 400px; text-align: center; top: 494px; font-size: 21px; font-weight: 700; color: var(--teal-band); }
  .stars { left: 412px; top: 531px; }
  .testimonials .brand-mark { right: 32px; bottom: 14px; font-size: 28px; color: var(--white); }

  /* slide 4 */
  .team { top: 1922px; }
  .team h2 { left: 0; width: 1040px; text-align: center; top: 36px; font-size: 50px; color: var(--white); font-weight: 700; }
  .card { position: absolute; top: 168px; width: 236px; height: 295px; background: var(--white); border-radius: 6px; text-align: center; }
  .card .avatar { position: absolute; left: 70px; top: -48px; width: 96px; height: 96px; border-radius: 50%; border: 2px solid var(--white); box-sizing: border-box; background: linear-gradient(160deg, #c9a78d, #5c4a40); }
  .card h3 { margin: 60px 0 0; font-size: 22px; color: var(--blue); font-weight: 700; }
  .card .role { margin: 6px 0 0; font-size: 16px; color: var(--teal); font-weight: 700; }
  .card p.bio { margin: 8px auto 0; width: 205px; font-size: 12.5px; line-height: 22.5px; color: var(--text); }
  .team .brand-mark { right: 32px; bottom: 14px; font-size: 28px; color: var(--white); }

  /* slide 5 */
  .services { top: 2548px; background: linear-gradient(120deg, #eef1f3, #e3e8ec 50%, #eef1f3); }
  .services h2 { left: 0; width: 1040px; text-align: center; top: 36px; font-size: 50px; color: var(--teal); font-weight: 700; }
  .services .brand-mark { right: 32px; bottom: 14px; font-size: 28px; color: var(--ink); }

  /* slide 6 */
  .thanks { top: 3174px; }
  .thanks .big-name { left: 128px; top: 385px; font-size: 135px; color: #1e3a4a; line-height: 1; }
  .thanks .small-name { left: 620px; top: 128px; font-size: 30px; color: var(--white); font-weight: 700; }
  .thanks h2 { left: 620px; top: 194px; font-size: 32px; color: var(--white); font-weight: 700; }
  .thanks .body { left: 620px; top: 250px; width: 370px; font-size: 9px; line-height: 22px; color: var(--white); }
  .contact { left: 620px; top: 356px; list-style: none; padding: 0; color: var(--white); font-size: 17px; }
  .contact li { display: flex; align-items: center; height: 38.5px; }
  .contact svg { width: 16px; height: 16px; margin-right: 12px; fill: var(--white); flex: none; }
  .contact .indent { padding-left: 28px; }
</style>
</head>
<body>
<div class="canvas">

  <!-- Welcome -->
  <section class="slide welcome photo-teal" role="img" aria-label="Team photo of smiling staff tinted in brand teal">
    <h1 class="abs">Welcome to VLT</h1>
    <p class="abs lead">Where we maintain a passion for excellence, striving to be better each and every day,<br>so that our guests leave happy and our team members feel fulfilled.</p>
    <div class="abs social"><span></span><span></span><span></span><span></span></div>
    <div class="abs brand-mark big-name">VLT</div>
  </section>

  <!-- About -->
  <section class="slide about">
    <svg class="abs" style="left:0;top:0" width="1040" height="584" viewBox="0 0 1040 584">
      <polygon points="0,0 478,0 610,584 0,584" fill="#6b5a48" role="img" aria-label="Photo of three colleagues laughing over coffee at a cafe table"/>
      <polygon points="478,0 530,0 662,584 610,584" fill="var(--blue)"/>
      <polygon points="428,127 470,121 548,484 505,490" fill="var(--teal-band)"/>
      <polygon points="468,238 506,232 560,525 522,531" fill="var(--teal-band)"/>
    </svg>
    <h2 class="abs">ABOUT US</h2>
    <p class="abs body">VLT is dedicated to cultivating a positive culture of leadership for its team members' professional and personal development, and this person-focused mentality transfers throughout the company from partners to our teams to guests. We strive to ensure each team member feels valued in all aspects of their role, reinforcing the importance of fostering a self-sustaining culture of success where everyone makes a team effort to communicate and overcome adversity.</p>
    <span class="brand-mark">VLT</span>
  </section>

  <!-- Testimonials -->
  <section class="slide testimonials">
    <svg class="abs" style="left:0;top:0" width="1040" height="584" viewBox="0 0 1040 584">
      <rect width="1040" height="584" fill="#2d6a78" role="img" aria-label="Photos of cheerful guests tinted in brand blue and teal"/>
      <polygon points="390,0 1030,0 617,584 0,584" fill="var(--white)"/>
      <line x1="370" y1="20" x2="48" y2="500" stroke="var(--blue)" stroke-width="46"/>
      <line x1="400" y1="60" x2="215" y2="325" stroke="var(--teal-band)" stroke-width="40"/>
      <line x1="955" y1="20" x2="785" y2="280" stroke="var(--blue)" stroke-width="46"/>
      <line x1="1030" y1="35" x2="680" y2="490" stroke="var(--teal-band)" stroke-width="34"/>
    </svg>
    <h2 class="abs">TESTIMONIALS</h2>
    <div class="abs quote-mark" style="top:160px;">&ldquo;</div>
    <p class="abs body">Lorem ipsum dolor sit amet, consectetur adipiscing elit, sed do eiusmod tempor incididunt ut labore et dolore magna aliqua. Ut enim ad minim veniam, quis nostrud exercitation ullamco laboris nisi ut aliquip ex ea commodo consequat. Duis aute irure dolor in reprehenderit in voluptate velit esse cillum dolore eu fugiat nulla pariatur. Excepteur sint occaecat cupidatat non proident, sunt in culpa qui officia deserunt mollit anim id est laborum.</p>
    <div class="abs quote-mark" style="top:458px;">&rdquo;</div>
    <div class="abs tag">CARE AND PROFESSIONALISM</div>
    <svg class="abs stars" width="110" height="20" viewBox="0 0 110 20">
      <g fill="var(--star)">
        <polygon id="star" points="9,1 11.3,6.8 17.5,7 12.6,10.9 14.3,17 9,13.5 3.7,17 5.4,10.9 0.5,7 6.7,6.8"/>
        <use href="#star" x="23"/><use href="#star" x="46"/><use href="#star" x="69"/><use href="#star" x="92"/>
      </g>
    </svg>
    <span class="brand-mark">VLT</span>
  </section>

  <!-- Team -->
  <section class="slide team photo-teal">
    <h2 class="abs">MEET THE TEAM</h2>
    <div class="card" style="left:124px;">
      <div class="avatar" role="img" aria-label="Portrait of the CEO"></div>
      <h3>KEVIN GARNER</h3>
      <p class="role">CEO</p>
      <p class="bio">Growing up in Wichita, Kansas, where Frankie's started, Kevin has long felt a connection with the group that started the concept, enjoying the food, culture, and opportunity to be a part of this incredible brand.</p>
    </div>
    <div class="card" style="left:402px;">
      <div class="avatar" role="img" aria-label="Portrait of the controller"></div>
      <h3>PAIGE AMBROSE</h3>
      <p class="role">CONTROLLER</p>
      <p class="bio">Paige Ambrose is a brilliant veteran of the finance and accounting industries, utilizing her experience to elevate VLT and its team members and customers. With two years (and counting) under her belt.</p>
    </div>
    <div class="card" style="left:680px;">
      <div class="avatar" role="img" aria-label="Portrait of the COO"></div>
      <h3>DEAN TURNER</h3>
      <p class="role">COO</p>
      <p class="bio">Growing up in Wichita, Kansas, where Frankie's started, Dean has long felt a connection with the group that started the concept, enjoying the food, culture, and opportunity to be a part of this incredible brand.</p>
    </div>
    <span class="brand-mark">VLT</span>
  </section>

  <!-- What we do -->
  <section class="slide services" role="img" aria-label="Faint group photo of the team behind a three-part service diagram">
    <h2 class="abs">WHAT WE DO</h2>
    <svg class="abs" style="left:0;top:0" width="1040" height="584" viewBox="0 0 1040 584" font-family="Arimo, Helvetica, Arial, sans-serif">
      <defs>
        <marker id="head-blue" markerWidth="8" markerHeight="8" refX="6" refY="4" orient="auto"><path d="M0,0 L8,4 L0,8 z" fill="var(--royal)"/></marker>
        <marker id="head-green" markerWidth="8" markerHeight="8" refX="6" refY="4" orient="auto"><path d="M0,0 L8,4 L0,8 z" fill="var(--green)"/></marker>
        <marker id="head-teal" markerWidth="8" markerHeight="8" refX="6" refY="4" orient="auto"><path d="M0,0 L8,4 L0,8 z" fill="var(--teal)"/></marker>
      </defs>
      <polygon points="530,188 694,478 366,478" fill="var(--blue)"/>
      <text x="537" y="450" text-anchor="middle" font-size="56" font-weight="700" fill="var(--white)">VLT</text>
      <line x1="359" y1="405" x2="469" y2="226" stroke="var(--royal)" stroke-width="2" marker-end="url(#head-blue)"/>
      <line x1="585" y1="214" x2="692" y2="393" stroke="var(--green)" stroke-width="2" marker-end="url(#head-green)"/>
      <line x1="632" y1="501" x2="428" y2="501" stroke="var(--teal)" stroke-width="2" marker-end="url(#head-teal)"/>
      <text x="0" y="0" transform="translate(390,325) rotate(-58)" text-anchor="middle" font-size="16" font-weight="700" fill="var(--royal)">DEVELOPMENT</text>
      <text x="0" y="0" transform="translate(660,292) rotate(60)" text-anchor="middle" font-size="16" font-weight="700" fill="var(--green)">RESTAURANTS</text>
      <text x="526" y="529" text-anchor="middle" font-size="16" font-weight="700" fill="var(--teal)">REAL ESTATE</text>
      <circle cx="531" cy="180" r="47" fill="var(--green)"/>
      <text x="531" y="193" text-anchor="middle" font-size="36" font-weight="700" fill="var(--white)">01</text>
      <circle cx="350" cy="462" r="47" fill="var(--royal)"/>
      <text x="350" y="475" text-anchor="middle" font-size="36" font-weight="700" fill="var(--white)">03</text>
      <circle cx="708" cy="462" r="47" fill="var(--cyan)"/>
      <text x="708" y="475" text-anchor="middle" font-size="36" font-weight="700" fill="var(--white)">03</text>
    </svg>
    <span class="brand-mark">VLT</span>
  </section>

  <!-- Thank you -->
  <section class="slide thanks photo-teal" role="img" aria-label="Group photo of team members tinted in brand teal">
    <div class="abs brand-mark big-name">VLT</div>
    <div class="abs small-name">VLT</div>
    <h2 class="abs">THANK YOU</h2>
    <p class="abs body">VLT is dedicated to cultivating a positive culture of leadership for its team members' professional and personal development, and this person-focused mentality transfers throughout the company from partners to our teams to guests. We strive to ensure each team member feels valued</p>
    <ul class="abs contact">
      <li><svg viewBox="0 0 16 16"><path d="M3.5 1l2.6 3-1.4 1.8c.9 2 2.5 3.6 4.5 4.5L11 8.9l3 2.6-1.2 2.8C7 14 2 9 1.7 2.2z"/></svg>+1 555 014 2290</li>
      <li><svg viewBox="0 0 16 16"><path d="M8 1a7 7 0 100 14A7 7 0 008 1zm0 1.5c.8 0 1.8 1.6 2.1 4H5.9C6.2 4.1 7.2 2.5 8 2.5zM2.6 7.3h2.2a12 12 0 000 1.4H2.6a5.5 5.5 0 010-1.4zm3.3 2.2h4.2c-.3 2.4-1.3 4-2.1 4s-1.8-1.6-2.1-4zm5.3-2.2h2.2a5.5 5.5 0 010 1.4h-2.2a12 12 0 000-1.4z"/></svg>https://www.crewvlt.com/</li>
      <li><svg viewBox="0 0 16 16"><path d="M1 3h14v1.2L8 9 1 4.2zm0 2.8l7 4.8 7-4.8V13H1z"/></svg>hello@crewvlt.com</li>
      <li><svg viewBox="0 0 16 16"><path d="M8 1a5 5 0 00-5 5c0 3.8 5 9 5 9s5-5.2 5-9a5 5 0 00-5-5zm0 7a2 2 0 110-4 2 2 0 010 4z"/></svg>4120 N. CEDAR RIDGE SUITE 210</li>
      <li class="indent">DENVER, CO 80211</li>
    </ul>
  </section>

</div>
</body>
</html>
```